We are a local Communty Pharmacy wishing to promote and market a specialised Pharmaceutical Service

We would like a design that is professional and enticing ( according to the brief In attached files)
We wish to Market Brookvale Compounding as a specialist side of our business.
We have the expertise a purpose built preparation laboratory.
The main purpose is an Internet presence that entices prospective patients to contact or visit our physical store.

Target Market(s)

Patients Medicos and Veterinary clients

Industry/Entity Type

Pharmacy

Coding

Coded - Design and coding required

Number of Pages Required

1 page

Requirements
Must have
• Clear friendly image
Nice to have
• soft enticing feel
Should not have
• No crass loud unprofessional elements

```html
<!DOCTYPE html>
<html lang="en">
<head>
<meta charset="utf-8">
<title>Brookvale Compounding</title>
<link href="https://fonts.googleapis.com/css2?family=Open+Sans:wght@400;600;700;800&display=swap" rel="stylesheet">
<style>
:root{
  --blue:#3a78d6;
  --blue-deep:#2a5fb8;
  --card:rgba(52,108,210,.92);
  --ink:#333;
  --muted:#777;
  --topbar:#1c1e22;
  --footer:#232427;
  --footer-base:#151618;
  --line:#e3e3e3;
}
*{box-sizing:border-box;margin:0;padding:0}
html,body{width:776px;height:1200px;overflow:hidden}
body{font-family:"Open Sans",Arial,sans-serif;color:var(--ink);background:#fff;font-size:9px;line-height:1.5}
.topbar{height:28px;background:var(--topbar);color:#bbb;display:flex;align-items:center;gap:18px;padding:0 60px;font-size:8.5px}
.topbar span{display:flex;align-items:center;gap:5px}
.header{height:70px;display:flex;align-items:center;justify-content:space-between;padding:0 60px;border-bottom:1px solid var(--line)}
.brand{display:flex;align-items:center;gap:9px;color:var(--blue);font-weight:800;font-size:15px;letter-spacing:.5px;text-transform:uppercase}
.brand-dot{width:24px;height:24px;border-radius:50%;background:var(--blue)}
.nav{display:flex;align-items:center;gap:6px;font-size:8.5px;font-weight:600;text-transform:uppercase}
.nav a{color:#555;text-decoration:none;padding:6px 12px}
.nav a.active{border:1px solid var(--blue);color:var(--blue)}
.hero{position:relative;height:415px}
.hero-photo{position:absolute;inset:0;background:linear-gradient(100deg,#6d8aa3 0%,#a9bccb 35%,#dfe6ec 60%,#c7b8a9 100%)}
.hero-title{position:absolute;left:60px;top:150px;color:#fff;font-weight:800;font-size:21px;line-height:1.3;text-transform:uppercase;text-shadow:0 1px 3px rgba(0,0,0,.35)}
.features{position:absolute;left:60px;right:60px;top:268px;display:flex;gap:10px}
.feature{flex:1;height:140px;background:var(--card);color:#fff;padding:14px 14px}
.feature h3{display:flex;align-items:center;gap:8px;font-size:9px;font-weight:700;text-transform:uppercase;margin-bottom:9px}
.feature-icon{width:26px;height:26px;border-radius:50%;background:#fff;display:flex;align-items:center;justify-content:center;flex:none}
.feature p{font-size:7.5px;line-height:1.55;color:#e6eefc;margin-bottom:11px}
.btn{display:inline-block;font-size:7px;font-weight:700;text-transform:uppercase;padding:5px 11px;border-radius:3px}
.btn-light{border:1px solid #fff;color:#fff}
.btn-blue{background:var(--blue);color:#fff}
.welcome{display:flex;gap:24px;padding:20px 60px 0;height:222px}
.welcome-photo{width:250px;height:180px;flex:none;background:linear-gradient(135deg,#d9e5ee,#b6cbd9 55%,#e8eef2)}
.welcome h2{font-size:17px;font-weight:700;text-transform:uppercase;color:#333;margin-bottom:8px}
.welcome h2 em{font-style:normal;color:var(--blue)}
.welcome p{font-size:7.8px;color:var(--muted);line-height:1.6;margin-bottom:8px}
.posts{padding:6px 60px 0;height:240px}
.section-title{text-align:center;font-size:17px;font-weight:700;text-transform:uppercase;color:#333}
.section-rule{width:44px;height:2px;background:var(--blue);margin:6px auto 24px}
.post-list{display:flex;gap:30px}
.post{flex:1;display:flex;gap:12px}
.post-photo{width:110px;height:100px;flex:none;border:3px solid #eee;background:linear-gradient(135deg,#e9eff3,#c5d5e1)}
.post h4{font-size:9px;font-weight:700;color:var(--blue);margin-bottom:2px}
.post time{display:block;font-size:7px;color:#999;margin-bottom:5px}
.post p{font-size:7.5px;color:var(--muted);line-height:1.55;margin-bottom:5px}
.post a{font-size:7.5px;color:var(--blue);text-decoration:none;font-weight:600}
.footer{background:var(--footer);height:172px;padding:22px 60px 0;display:flex;gap:24px;color:#bbb}
.footer-col{flex:1}
.footer-col h5{color:#fff;font-size:9px;font-weight:700;text-transform:uppercase;margin-bottom:12px}
.footer-col ul{list-style:none;font-size:7.5px}
.footer-col li{margin-bottom:5px;display:flex;align-items:center;gap:6px}
.footer-col li::before{content:"";width:3px;height:3px;background:#888;border-radius:50%}
.map{width:140px;height:95px;background:linear-gradient(135deg,#e6e8e1,#cfd6cc)}
.contact-line{display:flex;align-items:center;gap:7px;font-size:7.5px;margin-bottom:8px}
.contact-line strong{color:#fff;font-size:11px}
.social li::before{width:9px;height:9px;background:#666}
.footer-base{height:25px;background:var(--footer-base);color:#888;font-size:7px;display:flex;align-items:center;justify-content:center}
</style>
</head>
<body>
<div class="topbar">
  <span><svg width="9" height="9" viewBox="0 0 24 24"><path fill="#bbb" d="M6.6 10.8a15 15 0 0 0 6.6 6.6l2.2-2.2c.3-.3.7-.4 1-.2 1.1.4 2.3.6 3.6.6.6 0 1 .4 1 1V20c0 .6-.4 1-1 1A17 17 0 0 1 3 4c0-.6.4-1 1-1h3.5c.6 0 1 .4 1 1 0 1.3.2 2.5.6 3.6.1.3 0 .7-.2 1z"/></svg>555-0142</span>
  <span><svg width="10" height="8" viewBox="0 0 24 18"><rect x="1" y="1" width="22" height="16" fill="none" stroke="#bbb" stroke-width="2"/><path d="M1 1l11 9 11-9" fill="none" stroke="#bbb" stroke-width="2"/></svg>hello@brookvalecompounding.example</span>
</div>
<header class="header">
  <div class="brand"><span class="brand-dot"></span>Brookvale Compounding</div>
  <nav class="nav">
    <a class="active">Home</a><a>About Us</a><a>Locations</a><a>Timings</a><a>Contact</a>
    <svg width="12" height="12" viewBox="0 0 24 24"><circle cx="10" cy="10" r="6.5" fill="none" stroke="#555" stroke-width="2.4"/><path d="M15 15l6 6" stroke="#555" stroke-width="2.6"/></svg>
  </nav>
</header>
<section class="hero">
  <div class="hero-photo" role="img" aria-label="Photo of a smiling pharmacist in a white coat in a pharmacy aisle, with a colleague beside the shelves"></div>
  <h1 class="hero-title">Pharmacists the unique ability to<br>compound medicines</h1>
  <div class="features">
    <div class="feature">
      <h3><span class="feature-icon"><svg width="12" height="14" viewBox="0 0 12 14"><rect x="3.5" y="0" width="5" height="2.5" fill="#3a78d6"/><rect x="1.5" y="3.5" width="9" height="10.5" rx="1.5" fill="#3a78d6"/></svg></span>Medicine Bottle</h3>
      <p>Liquid forms made to order in our lab, flavoured and dosed for each patient.</p>
      <span class="btn btn-light">More Info</span>
    </div>
    <div class="feature">
      <h3><span class="feature-icon"><svg width="14" height="8" viewBox="0 0 14 8"><rect x="0" y="0" width="14" height="8" rx="4" fill="#3a78d6"/><path d="M7 0v8" stroke="#fff" stroke-width="1"/></svg></span>Tablet</h3>
      <p>Tablets and capsules made to exact strengths when standard doses do not fit.</p>
      <span class="btn btn-light">More Info</span>
    </div>
    <div class="feature">
      <h3><span class="feature-icon"><svg width="13" height="14" viewBox="0 0 13 14"><path d="M4.5 0h4v5l4 8H.5l4-8z" fill="#3a78d6"/></svg></span>Pharmaceutical</h3>
      <p>Expert pharmacists prepare creams, gels and drops in a purpose built lab.</p>
      <span class="btn btn-light">More Info</span>
    </div>
    <div class="feature">
      <h3><span class="feature-icon"><svg width="14" height="10" viewBox="0 0 14 10"><path d="M0 2h14a7 7 0 0 1-14 0z" fill="#3a78d6"/></svg></span>Medicines Bowl</h3>
      <p>Veterinary mixes prepared for pets, with easy doses and flavours they accept.</p>
      <span class="btn btn-light">More Info</span>
    </div>
  </div>
</section>
<section class="welcome">
  <div class="welcome-photo" role="img" aria-label="Photo of a pharmacist holding a medicine box at the pharmacy counter"></div>
  <div>
    <h2>Welcome to <em>Brookvale Compounding</em></h2>
    <p>Our pharmacy has served the local community for many years. Compounding is the art of preparing a medicine made just for one patient, when a standard product is not right. We work with doctors, vets and patients to create doses, strengths and forms that suit each person. From flavoured liquids for children to creams without allergens, our trained team prepares every item with care in our purpose built laboratory.</p>
    <p>Visit our store or call us to talk about how a compounded medicine could help you or your pet.</p>
    <span class="btn btn-blue">Learn More</span>
  </div>
</section>
<section class="posts">
  <h2 class="section-title">Recent Posts</h2>
  <div class="section-rule"></div>
  <div class="post-list">
    <article class="post">
      <div class="post-photo" role="img" aria-label="Photo of a pharmacist with a tablet in the dispensary"></div>
      <div>
        <h4>Nemo Enim Ipsam Voluptatem</h4>
        <time>July 5th, 2015</time>
        <p>We prepare custom medicines for patients who need a different dose, form or flavour. Ask our team how this can help.</p>
        <a>Read more →</a>
      </div>
    </article>
    <article class="post">
      <div class="post-photo" role="img" aria-label="Photo of a pharmacist smiling at a customer across the counter"></div>
      <div>
        <h4>Nemo Enim Ipsam Voluptatem</h4>
        <time>July 5th, 2015</time>
        <p>We prepare custom medicines for patients who need a different dose, form or flavour. Ask our team how this can help.</p>
        <a>Read more →</a>
      </div>
    </article>
  </div>
</section>
<footer class="footer">
  <div class="footer-col">
    <h5>Navigation</h5>
    <ul><li>Home</li><li>About Us</li><li>Locations</li><li>Timings</li><li>Contact</li></ul>
  </div>
  <div class="footer-col">
    <h5>Location</h5>
    <div class="map" role="img" aria-label="Street map showing the pharmacy location"></div>
  </div>
  <div class="footer-col">
    <h5>Contact Us</h5>
    <div class="contact-line"><svg width="9" height="12" viewBox="0 0 12 16"><path d="M6 0a6 6 0 0 1 6 6c0 4-6 10-6 10S0 10 0 6a6 6 0 0 1 6-6z" fill="#3a78d6"/><circle cx="6" cy="6" r="2.2" fill="#232427"/></svg>14 Alder Lane, Maplewood</div>
    <div class="contact-line"><svg width="11" height="11" viewBox="0 0 24 24"><path fill="#3a78d6" d="M6.6 10.8a15 15 0 0 0 6.6 6.6l2.2-2.2c.3-.3.7-.4 1-.2 1.1.4 2.3.6 3.6.6.6 0 1 .4 1 1V20c0 .6-.4 1-1 1A17 17 0 0 1 3 4c0-.6.4-1 1-1h3.5c.6 0 1 .4 1 1 0 1.3.2 2.5.6 3.6.1.3 0 .7-.2 1z"/></svg><strong>555-0142</strong></div>
    <div class="contact-line"><svg width="11" height="9" viewBox="0 0 24 18"><rect x="1" y="1" width="22" height="16" fill="none" stroke="#3a78d6" stroke-width="2"/><path d="M1 1l11 9 11-9" fill="none" stroke="#3a78d6" stroke-width="2"/></svg>hello@brookvalecompounding.example</div>
  </div>
  <div class="footer-col">
    <h5>Social Media</h5>
    <ul class="social"><li>Friendwall</li><li>Quickpost</li><li>Circleboard</li><li>Clipstream</li></ul>
  </div>
</footer>
<div class="footer-base">© 2015 Brookvale Compounding. All Rights Reserved.</div>
</body>
</html>
```